Post Disaster Temporary Housing Literature Review poster

Wanting a poster design for two Emergency Management conferences we have coming up. The information to be included in the poster is capturing the purpose, findings and recommendations from a post disaster temporary housing literature review looking at “What should government consider in order to improve planning and decision making for accommodation needs after a disaster, and to support people’s transition to stable housing?”
I’d like to enhance the visual appeal through including relevant images or graphic. I am also open to reducing the text if needed.
The government group I work with focuses on the social and human side of disaster recovery so keen for any images to reflect the human aspect and not focus solely on disasters or housing.
Government and NGO's

```html
<!DOCTYPE html>
<html lang="en">
<head>
<meta charset="utf-8">
<title>Post Disaster Temporary Housing – Literature Review Poster</title>
<link rel="stylesheet" href="https://fonts.googleapis.com/css2?family=Bebas+Neue&family=Great+Vibes&family=Poppins:wght@400;600&display=swap">
<style>
  :root{
    --stage:#a8a8a8;
    --ink:#ffffff;
    --sky:#00a3dc;
    --sky-light:#4fb9e3;
    --night:#131313;
    --photo-gold:#a88a45;
    --photo-olive:#5a5a3e;
    --photo-dark:#2a2a22;
    --hands-brown:#6b4a35;
    --globe-blue:#2f7fae;
  }
  *{box-sizing:border-box;margin:0;padding:0}
  html,body{width:1200px;height:876px;overflow:hidden;background:var(--stage)}
  body{position:relative;font-family:"Poppins",sans-serif;color:var(--ink)}
  .page{position:absolute;top:71px;width:519px;height:734px;overflow:hidden}

  /* Cover page */
  .cover{left:69px}
  .cover-photo{position:absolute;inset:0 0 94px 0;
    background:
      linear-gradient(180deg,rgba(0,0,0,0) 0%,rgba(0,0,0,0) 70%,rgba(120,40,25,.55) 86%,rgba(60,30,20,.8) 100%),
      linear-gradient(180deg,var(--photo-gold) 0%,var(--photo-olive) 30%,var(--photo-dark) 60%,#3a3324 100%)}
  .cover-shade{position:absolute;left:0;right:0;top:290px;height:270px;background:rgba(25,25,20,.55)}
  .title{position:absolute;left:0;right:0;text-align:center;font-family:"Bebas Neue",sans-serif;line-height:1;letter-spacing:.5px}
  .title-1{top:56px;font-size:68px}
  .title-2{top:124px;font-size:68px}
  .title-script{position:absolute;left:50px;top:146px;font-family:"Great Vibes",cursive;font-size:78px;color:var(--sky-light);transform:rotate(-6deg);white-space:nowrap;line-height:1}
  .intro-heading{position:absolute;top:300px;font-family:"Bebas Neue",sans-serif;font-size:19px;letter-spacing:.3px}
  .intro-text{position:absolute;top:328px;font-size:10.6px;line-height:13px}
  .purpose{left:25px;width:215px}
  .question{left:281px;width:215px}
  .intro-divider{position:absolute;left:260px;top:303px;height:155px;border-left:1px dashed rgba(255,255,255,.7)}
  .contact-band{position:absolute;left:0;right:0;bottom:0;height:94px;background:var(--sky)}
  .contact-line{position:absolute;left:51px;font-family:"Bebas Neue",sans-serif;font-size:17.5px;line-height:1;letter-spacing:.2px}
  .contact-icon{position:absolute;left:24px}
  .org-mark{position:absolute;left:360px;top:30px;display:flex;align-items:center;gap:8px}
  .org-mark span{font-size:9.5px;line-height:12px;width:100px}

  /* Findings page */
  .findings-page{left:612px;background:var(--night)}
  .script-heading{position:absolute;left:25px;font-family:"Great Vibes",cursive;font-size:26px;color:var(--sky-light)}
  .finding-card{position:absolute;top:59px;width:149px;height:227px;border:1px solid var(--sky-light);border-radius:7px;padding:17px 6px 0 8px}
  .finding-card h3{font-size:10.4px;line-height:12.3px;font-weight:600;color:var(--sky-light);margin-bottom:5px}
  .finding-card p{font-size:10.1px;line-height:12.3px;margin-bottom:7px}
  .finding-card.tight p{line-height:10.5px;margin-bottom:5px}
  .rec{position:absolute;left:26px;width:285px}
  .rec h4{font-size:10.6px;font-weight:600;line-height:13px;margin-bottom:6px}
  .rec p{font-size:10.6px;line-height:14px}
  .hands-globe{position:absolute;left:335px;top:288px;width:148px;height:143px;
    background:linear-gradient(160deg,var(--hands-brown) 0%,var(--globe-blue) 50%,var(--hands-brown) 100%)}
  .next-steps{position:absolute;left:317px;top:431px;width:183px;height:303px;background:var(--sky);border-radius:21px 0 0 0;padding:18px 0 0 19px}
  .next-steps h4{font-size:12.6px;font-weight:600;margin-bottom:4px}
  .next-steps p{font-size:12.4px;line-height:15.7px;width:160px}
</style>
</head>
<body>

<section class="page cover">
  <div class="cover-photo" role="img" aria-label="Moody street scene of a damaged town with a crowd of people in colourful shawls walking away"></div>
  <div class="cover-shade"></div>
  <h1 class="title title-1">Post Disaster</h1>
  <div class="title title-2">Temporary Housing</div>
  <div class="title-script">Literature Review</div>

  <h2 class="intro-heading purpose">Purpose</h2>
  <p class="intro-text purpose">The report addresses the significant challenges in providing timely and equitable emergency and temporary accommodation for displaced people &amp; assisting them towards stable housing after a disaster. It aims to help agencies and decision-makers develop effective post-disaster housing strategies, considering the disaster scale and community diversity.</p>
  <div class="intro-divider"></div>
  <h2 class="intro-heading question">Central Research Question</h2>
  <p class="intro-text question" style="top:331px">What should governments consider to improve planning and decision-making for post-disaster accommodation needs and support the transition to stable housing?</p>

  <footer class="contact-band">
    <svg class="contact-icon" style="top:19px" width="13" height="15" viewBox="0 0 13 15"><circle cx="6.5" cy="4" r="3.5" fill="#fff"/><path d="M0 15c0-4 3-6 6.5-6s6.5 2 6.5 6z" fill="#fff"/></svg>
    <div class="contact-line" style="top:19px">Helen Marlowe</div>
    <div class="contact-line" style="top:39px">National Consultant Disaster Recovery</div>
    <svg class="contact-icon" style="top:62px" width="11" height="14" viewBox="0 0 11 14"><path d="M0 0l10 8H5.5l2.5 5-2 1-2.5-5L0 12z" fill="#fff"/></svg>
    <div class="contact-line" style="top:60px">helen.marlowe@renewal.example.gov.au</div>
    <div class="org-mark">
      <svg width="30" height="30" viewBox="0 0 30 30"><circle cx="15" cy="15" r="13" fill="none" stroke="#fff" stroke-width="1.5"/></svg>
      <span>Community Recovery Council Australia</span>
    </div>
  </footer>
</section>

<section class="page findings-page">
  <h2 class="script-heading" style="top:22px">Findings</h2>

  <article class="finding-card" style="left:18px">
    <h3>Leading Practice in Disaster Housing Recovery:</h3>
    <p>Community Engagement &amp; Participation.</p>
    <p>Location.</p>
    <p>Safety, Health, Comfort &amp; Privacy.</p>
    <p>Cultural &amp; Special Needs</p>
    <p>Community &amp;<br>Connection<br>Social &amp; Technical<br>Support Services.</p>
  </article>
  <article class="finding-card" style="left:184px">
    <h3>Innovative Approaches to Temporary Housing:</h3>
    <p>Prioritizing post-disaster housing and infrastructure planning in pre-disaster preparation.</p>
    <p>Establishing Temporary Housing as a precursor to on-site Stable Housing to reduce social, economic, and environmental costs.</p>
  </article>
  <article class="finding-card tight" style="left:351px">
    <h3>Decision-Making for Resilient Housing Recovery:</h3>
    <p>Pre-Disaster Planning and Situation Analysis.</p>
    <p>Recognizing &amp; Addressing Diverse Needs.</p>
    <p>Housing Model Selection and Design.</p>
    <p>Support Services and Local Recovery Promotion.</p>
    <p>Monitoring and Evaluation.</p>
  </article>

  <div class="hands-globe" role="img" aria-label="Photo of cupped hands holding the Earth"></div>

  <h2 class="script-heading" style="top:298px">Recommendations</h2>
  <div class="rec" style="top:328px"><h4>Standard Terminology and Principles:</h4><p>Develop standard terms for accommodation phases and adopt leading practice principles: community connection, wellbeing, liveability, viability, and sustainability.</p></div>
  <div class="rec" style="top:417px"><h4>Resilient Recovery and Guidelines:</h4><p>Extend disaster recovery principles to include resilient recovery and create guidelines for post-disaster temporary housing planning.</p></div>
  <div class="rec" style="top:492px"><h4>Capacity Building and Funding:</h4><p>Develop resources and programs for pre-disaster planning and address indirect costs with targeted funding streams.</p></div>
  <div class="rec" style="top:567px"><h4>Research and Pilot Projects:</h4><p>Conduct research on housing resilience, past disaster learnings, and innovative construction methods. Evaluate a pilot program for a two-phase approach to stable housing.</p></div>
  <div class="rec" style="top:656px"><h4>Framework and Learning Repository:</h4><p>Adopt a decision-making framework for housing recovery and establish a national repository for evaluation reports and cross-case analysis.</p></div>

  <aside class="next-steps">
    <h4>Next Steps</h4>
    <p>The Community Recovery Council is collaborating with Hazard Resilience Research Institute to analyze past temporary housing assistance in Australia. The goal is to provide national guidance on designing and implementing temporary housing based on the findings &amp; resources developed.</p>
  </aside>
</section>

</body>
</html>
```